Business Card Design

New business card design

Target Market(s)

Residential & Commercial Property Managers

Industry/Entity Type

Plumbing Services

Contact Information for Business Card

Name - Rowan Keddle, title - Director, Phone Number - 0431 286 517, email - rowan@tbk-plumbing.com.au, Company ABN - 73 215 904 386,

Font styles to use
Sans Serif

Colors
0054AA
0677BA
7BADD7
CADEEF
E8F1F8

```html
<!DOCTYPE html>
<html lang="en">
<head>
<meta charset="utf-8">
<title>TBK Plumbing Services – Business Card</title>
<link rel="stylesheet" href="https://fonts.googleapis.com/css2?family=Montserrat:wght@400;700&display=swap">
<style>
  :root {
    --page-bg: #e9ecef;
    --card-dark: #1e242a;
    --card-light: #ffffff;
    --brand-blue: #2ba3dc;
    --text-dark: #1c2126;
    --text-on-dark: #ffffff;
    --shadow: rgba(20, 26, 32, 0.18);
  }
  * { box-sizing: border-box; margin: 0; padding: 0; }
  html, body {
    width: 1200px;
    height: 912px;
    overflow: hidden;
    background: var(--page-bg);
    font-family: "Montserrat", sans-serif;
  }
  .sheet {
    width: 1200px;
    height: 912px;
    display: flex;
    flex-direction: column;
    align-items: center;
    justify-content: center;
    gap: 44px;
  }
  .card {
    width: 620px;
    height: 379px;
    border-radius: 18px;
    overflow: hidden;
    box-shadow: 0 10px 28px var(--shadow);
    position: relative;
  }

  /* Front */
  .card--front {
    background: var(--card-dark);
    display: flex;
    align-items: center;
    justify-content: center;
  }
  .brand {
    display: flex;
    align-items: center;
    gap: 12px;
  }
  .brand__dot {
    width: 14px;
    height: 14px;
    border-radius: 50%;
    background: var(--brand-blue);
  }
  .brand__name {
    font-weight: 400;
    font-size: 26px;
    letter-spacing: 3px;
    color: #3a4249;
  }

  /* Back */
  .card--back {
    background: var(--card-light);
    display: flex;
  }
  .back__band {
    width: 190px;
    height: 100%;
    background: var(--card-dark);
    display: flex;
    align-items: center;
    justify-content: center;
  }
  .back__band .brand {
    transform: rotate(-90deg);
    white-space: nowrap;
  }
  .back__band .brand__name {
    color: var(--text-on-dark);
    font-size: 22px;
  }
  .back__info {
    flex: 1;
    padding: 92px 0 0 44px;
  }
  .person__name {
    font-weight: 700;
    font-size: 27px;
    color: var(--brand-blue);
    line-height: 1.1;
  }
  .person__title {
    font-size: 17px;
    color: var(--text-dark);
    margin-top: 2px;
  }
  .abn {
    margin-top: 44px;
    font-size: 15px;
    color: var(--text-dark);
  }
  .abn__label { color: var(--brand-blue); }
  .contact {
    list-style: none;
    margin-top: 12px;
    font-size: 16px;
    color: var(--text-dark);
  }
  .contact__item {
    display: flex;
    align-items: center;
    gap: 10px;
    margin-top: 6px;
  }
  .contact__icon { width: 14px; height: 14px; flex: none; }
</style>
</head>
<body>
  <main class="sheet">
    <section class="card card--front" aria-label="Card front">
      <div class="brand">
        <span class="brand__dot"></span>
        <span class="brand__name">TBK Plumbing Services</span>
      </div>
    </section>

    <section class="card card--back" aria-label="Card back">
      <div class="back__band">
        <div class="brand">
          <span class="brand__dot"></span>
          <span class="brand__name">TBK Plumbing Services</span>
        </div>
      </div>
      <div class="back__info">
        <h1 class="person__name">Rowan Keddle</h1>
        <p class="person__title">Director</p>
        <p class="abn"><span class="abn__label">Company ABN</span> - 73 215 904 386</p>
        <ul class="contact">
          <li class="contact__item">
            <svg class="contact__icon" viewBox="0 0 24 24" aria-hidden="true">
              <path fill="#2ba3dc" d="M6.6 10.8a15.1 15.1 0 0 0 6.6 6.6l2.2-2.2c.3-.3.7-.4 1-.2 1.1.4 2.3.6 3.6.6.6 0 1 .4 1 1V20c0 .6-.4 1-1 1A17 17 0 0 1 3 4c0-.6.4-1 1-1h3.5c.6 0 1 .4 1 1 0 1.3.2 2.5.6 3.6.1.3 0 .7-.2 1z"/>
            </svg>
            <span>0431 286 517</span>
          </li>
          <li class="contact__item">
            <svg class="contact__icon" viewBox="0 0 24 24" aria-hidden="true">
              <rect x="2" y="5" width="20" height="14" rx="1" fill="#2ba3dc"/>
              <path d="M2.5 6l9.5 7 9.5-7" fill="none" stroke="#ffffff" stroke-width="1.6"/>
            </svg>
            <span>rowan@tbk-plumbing.com.au</span>
          </li>
        </ul>
      </div>
    </section>
  </main>
</body>
</html>
```